Professional & attention grabbing.

A business card design, front and back. I already have a logo I will attach, but I am open to something new as well.
Things to include:
Name:
Title:
Phone:
Email:
Wanting something that is professional but attention grabbing.
Also we do a lot of work using drones on natural gas pipelines (leading the future)if you want to include any of that. I'm open to ideas.
Target Market(s)
Natural gas transmission industry / greenhouse gas mitigation industry
Industry/Entity Type
Business
Colors
Designer to choose colors to be used in the design.
Look and feel
Each slider illustrates characteristics of the customer's brand and the style your logo design should communicate.

```html
<!DOCTYPE html>
<html lang="en">
<head>
<meta charset="utf-8">
<title>Ridgeline Inspections – Business Card</title>
<link href="https://fonts.googleapis.com/css2?family=Ubuntu:wght@400;500;700&display=swap" rel="stylesheet">
<style>
  :root {
    --page-bg: #d9d6d1;
    --card-frost: #e9e8e6;
    --card-dark: #1c1c1e;
    --accent-red: #a3141c;
    --ink: #1e1e1e;
    --white: #ffffff;
  }
  html, body {
    margin: 0;
    width: 1200px;
    height: 969px;
    overflow: hidden;
    background: var(--page-bg);
    font-family: "Ubuntu", Arial, sans-serif;
  }
  .business-card {
    position: absolute;
    left: 100px;
    top: 200px;
    width: 1000px;
    height: 570px;
    border-radius: 24px;
    overflow: hidden;
    background: linear-gradient(135deg, #f1f0ee 0%, var(--card-frost) 60%, #dddbd8 100%);
    box-shadow: 0 18px 40px rgba(0,0,0,0.18);
  }
  .card-shapes {
    position: absolute;
    inset: 0;
  }
  .brand {
    position: absolute;
    left: 72px;
    top: 120px;
    display: flex;
    align-items: center;
    gap: 18px;
  }
  .brand-mark {
    width: 38px;
    height: 38px;
    background: var(--accent-red);
  }
  .brand-name {
    color: var(--white);
    font-weight: 500;
    font-size: 44px;
    letter-spacing: 1px;
  }
  .contact-block {
    position: absolute;
    right: 60px;
    top: 312px;
    text-align: right;
    color: var(--ink);
  }
  .person-name {
    margin: 0;
    color: var(--accent-red);
    font-weight: 700;
    font-size: 38px;
    letter-spacing: 1px;
  }
  .person-title {
    margin: 6px 0 40px;
    font-size: 28px;
  }
  .contact-list {
    list-style: none;
    margin: 0;
    padding: 0;
    font-size: 28px;
    line-height: 40px;
  }
  .contact-list li {
    display: flex;
    justify-content: flex-end;
    align-items: center;
    gap: 12px;
  }
  .contact-icon {
    width: 24px;
    height: 24px;
    fill: var(--accent-red);
  }
</style>
</head>
<body>
  <div class="business-card">
    <svg class="card-shapes" viewBox="0 0 1000 570" preserveAspectRatio="none">
      <defs>
        <linearGradient id="darkPanel" x1="0" y1="0" x2="1" y2="1">
          <stop offset="0" stop-color="#2a2a2c"/>
          <stop offset="1" stop-color="#111112"/>
        </linearGradient>
        <linearGradient id="redSwoosh" x1="0" y1="0" x2="0" y2="1">
          <stop offset="0" stop-color="#c21a22"/>
          <stop offset="1" stop-color="#8e1016"/>
        </linearGradient>
      </defs>
      <path class="swoosh-red" d="M640 0 H675 C760 150 650 420 300 570 H230 C600 390 720 140 640 0 Z" fill="url(#redSwoosh)"/>
      <path class="dark-panel" d="M0 0 H640 C715 125 610 385 240 570 H0 Z" fill="url(#darkPanel)"/>
      <path class="swoosh-line" d="M690 0 C775 150 675 420 325 570" fill="none" stroke="#1a1a1a" stroke-width="3"/>
    </svg>

    <div class="brand">
      <span class="brand-mark"></span>
      <span class="brand-name">Ridgeline Inspections</span>
    </div>

    <div class="contact-block">
      <h1 class="person-name">DANIEL REYES</h1>
      <p class="person-title">CEO/Founder</p>
      <ul class="contact-list">
        <li>555 201 7834
          <svg class="contact-icon" viewBox="0 0 24 24"><path d="M6.6 10.8a15 15 0 0 0 6.6 6.6l2.2-2.2a1 1 0 0 1 1-.25 11.4 11.4 0 0 0 3.6.57 1 1 0 0 1 1 1V20a1 1 0 0 1-1 1A17 17 0 0 1 3 4a1 1 0 0 1 1-1h3.5a1 1 0 0 1 1 1c0 1.25.2 2.45.57 3.57a1 1 0 0 1-.25 1z"/></svg>
        </li>
        <li>hello@ridgelineinsp.com
          <svg class="contact-icon" viewBox="0 0 24 24"><path d="M2 5h20v14H2z M3 6l9 7 9-7" fill="none" stroke="#a3141c" stroke-width="0"/><path d="M2 5h20v2l-10 7L2 7z M2 9l10 7 10-7v10H2z"/></svg>
        </li>
        <li>www.ridgelineinsp.com
          <svg class="contact-icon" viewBox="0 0 24 24"><circle cx="12" cy="12" r="10"/><path d="M2 12h20M12 2c3 3 3 17 0 20M12 2c-3 3-3 17 0 20" fill="none" stroke="#e9e8e6" stroke-width="1.5"/></svg>
        </li>
      </ul>
    </div>
  </div>
</body>
</html>
```